Electrical Contractor Brochure, Folder and Letter Head

Brightwell Power Ltd. is an Edmonton based electrical contractor focusing on commercial and industrial electrical services. Our target market is manufacturing facilities, warehouses and commercial buildings.

We want to seem larger than we are with service vehicles and electricians ready to dispatch to service calls and new installations. Our key color is the blue in the logo. The BWP logo is well branded in Edmonton and should be on the brochure.

We are looking for a tri-fold brochure, full-page brochure with folder sleeves and a letter head.
Updates

Please ignore the second page of copy.  I only want the electrical content in the brochure.  This is my mistake.  Please use only the first page of copy.

Industry/Entity Type

Electrical

Requirements
Must have
• Many background pics of the services, electricians and projects. I like the faded BWP logo in the background of the letterhead! Folder Size A4
Nice to have
• Try the pic named Cover Pic1 to on the front of the brochure.
Should not have
• DO NOT USE ANY WEBSITE CONTENT. THIS IS NOT OUR BUSINESS. PLEASE USE ONLY CONTENT AND COLOR FROM THE ATTACHED FILES!!

```html
<!DOCTYPE html>
<html lang="en">
<head>
<meta charset="utf-8">
<title>Brightwell Power Ltd. – Tri-fold Brochure</title>
<link rel="stylesheet" href="https://fonts.googleapis.com/css2?family=Open+Sans:wght@400;600;700&display=swap">
<style>
  :root{
    --page-bg:#f2f2f2;
    --panel-dark:#2a292b;
    --panel-facet:#333234;
    --panel-facet-deep:#1f1e20;
    --brand-blue:#1d3f8f;
    --accent-blue:#2a9fe0;
    --text-light:#f4f4f4;
    --paper-white:#ffffff;
    --photo-shop-a:#c9c9c6;
    --photo-shop-b:#6f716f;
    --photo-field-a:#7d8a96;
    --photo-field-b:#3b4048;
    --pocket-a:#5a595c;
    --pocket-b:#242325;
  }
  *{box-sizing:border-box;margin:0;padding:0}
  html,body{width:1200px;height:905px;overflow:hidden;background:var(--page-bg)}
  body{font-family:"Open Sans",Arial,sans-serif;position:relative}
  .brochure{position:absolute;left:105px;top:170px;width:990px;height:560px;display:flex;box-shadow:0 18px 40px rgba(0,0,0,.25)}
  .panel{position:relative;width:330px;height:560px;background:var(--panel-dark);overflow:hidden}
  .panel + .panel{border-left:1px solid #1a191b}
  .panel-art{position:absolute;inset:0;width:100%;height:100%}
  .photo{position:absolute;left:0;top:0;width:100%}
  .photo-machine{height:140px;background:linear-gradient(160deg,var(--photo-shop-a),var(--photo-shop-b))}
  .photo-electrician{height:270px;background:linear-gradient(150deg,var(--photo-field-a),var(--photo-field-b))}
  .pocket{position:absolute;left:0;bottom:0;width:100%;height:70px;background:linear-gradient(180deg,var(--pocket-a),var(--pocket-b) 60%)}
  .brand-name{position:absolute;right:28px;top:30px;font-weight:700;font-size:46px;letter-spacing:2px;color:var(--brand-blue);line-height:1}
  .heading{position:absolute;font-weight:700;font-size:17px;color:var(--accent-blue);letter-spacing:.3px}
  .intro{position:absolute;font-size:11px;line-height:1.35;color:var(--text-light)}
  .service-list{position:absolute;list-style:none;font-size:11.5px;line-height:1.3;color:var(--text-light)}
  .left .heading{left:28px;top:128px}
  .left .intro{left:28px;top:160px;width:280px}
  .left .service-list{left:28px;top:228px}
  .middle .heading{left:30px;top:215px}
  .middle .intro{left:30px;top:248px;width:275px}
  .middle .service-list{left:30px;top:310px}
  .right .service-list{left:70px;top:330px}
</style>
</head>
<body>
<main class="brochure">
  <section class="panel left">
    <svg class="panel-art" viewBox="0 0 330 560" aria-hidden="true">
      <polygon points="0,300 330,150 330,470 0,470" fill="var(--panel-facet)"/>
      <path d="M0,0 H330 V130 Q170,60 0,95 Z" fill="var(--paper-white)"/>
      <path d="M0,95 Q170,60 330,130 L330,142 Q170,76 0,104 Z" fill="var(--brand-blue)"/>
    </svg>
    <div class="brand-name">BWP</div>
    <h2 class="heading">What We Do?</h2>
    <p class="intro">Brightwell Power Ltd. provides services that are vital to cost effective production and reducing costly down time with CNC and Conventional machines, Band Saws and Production equipment.</p>
    <ul class="service-list">
      <li>Mechanical and Electrical Troubleshooting</li>
      <li>PLC Troubleshooting</li>
      <li>Collision Recovery</li>
      <li>Machine Installations</li>
      <li>Machine Decommissioning</li>
      <li>Servo Diagnostics</li>
      <li>Preventive Maintenance Plans</li>
      <li>Inspections</li>
      <li>Parts Replacement</li>
      <li>Lubrication Oil Supply</li>
      <li>Parts Supply</li>
    </ul>
    <div class="pocket"></div>
  </section>

  <section class="panel middle">
    <div class="photo photo-machine" role="img" aria-label="Photo of a conventional lathe in a machine shop"></div>
    <svg class="panel-art" viewBox="0 0 330 560" aria-hidden="true">
      <polygon points="0,140 330,140 330,470 0,470" fill="var(--panel-facet)" opacity=".5"/>
      <path d="M0,130 Q160,150 330,200 L330,210 Q160,165 0,146 Z" fill="var(--brand-blue)"/>
      <path d="M0,146 Q160,165 330,210 L330,230 Q160,185 0,165 Z" fill="var(--panel-facet-deep)" opacity=".6"/>
    </svg>
    <h2 class="heading">Open for Business</h2>
    <p class="intro">Brightwell Power Ltd. provides services that are vital to cost effective production and reducing costly down time with CNC and Conventional machines, Band Saws and Production equipment.</p>
    <ul class="service-list">
      <li>Mechanical and Electrical Troubleshooting</li>
      <li>PLC Troubleshooting</li>
      <li>Collision Recovery</li>
      <li>Machine Installations</li>
      <li>Machine Decommissioning</li>
      <li>Servo Diagnostics</li>
    </ul>
    <div class="pocket"></div>
  </section>

  <section class="panel right">
    <div class="photo photo-electrician" role="img" aria-label="Photo of electricians in hard hats working on an industrial control panel"></div>
    <svg class="panel-art" viewBox="0 0 330 560" aria-hidden="true">
      <path d="M0,250 Q200,230 330,390 L330,560 L0,560 Z" fill="var(--panel-dark)"/>
      <path d="M0,240 Q210,215 330,370 L330,392 Q200,232 0,252 Z" fill="var(--brand-blue)"/>
    </svg>
    <ul class="service-list">
      <li>Machine Decommissioning</li>
      <li>Servo Diagnostics</li>
      <li>Preventive Maintenance Plans</li>
      <li>Inspections</li>
      <li>Parts Replacement</li>
      <li>Lubrication Oil Supply</li>
      <li>Parts Supply</li>
    </ul>
  </section>
</main>
</body>
</html>
```